Business Cards for IT Consulting Company (Managed Service Provider)

I am looking to have some business cards printed and would like some designs. We are an IT Consulting company based in Vancouver BC. I would like a nice clean and modern look to the cards. I have uploaded all the versions of my logo so parts can be used as needed. Here is a snippit from our website homepage:

Quillbrook Networks Ltd. is an IT Solutions Partner located in Vancouver BC, Canada. We offer IT solutions and support to customers in the greater Vancouver Area. With expertise in Microsoft platforms, as well as Linux and Mac OSX and over 12 years experience in the IT industry, Quillbrook Networks is dedicated to offering our clients top quality service and products. We take pride in the solutions we offer our customers. The greatest compliment a client can give us is to recommend our services.

Quillbrook Networks Ltd. offers a wide range of IT services from onsite service to remote support and managed service solutions. This allows clients to choose the support path that best suits their company’s needs. Supporting many different sized companies from small to enterprise level over the past 12 years Quillbrook Networks has the experience and expertise needed to ensure things run smoothly. Allowing our clients to focus on doing business.

Revolutionizing the way IT services are delivered.

Quillbrook Networks is dedicated to providing our clients with IT solutions that work and grow with them for years to come. This philosophy helps save money in the long run instead of replacing equipment constantly. Far too often IT solutions are not well thought out and while possibly solving the problem at hand, require replacement due to growth or quality within a very short time frame. Quillbrook Networks takes pride in providing solutions that will last and be able to accommodate growth without the need for replacement.

Industry/Entity Type

Information Technology

Contact Information for Business Card

Quillbrook Networks Ltd.
(Employee Name)
Eml: (Employees Email Address)
Web: quillbrook.me
Ph: 604-555-0148

Font styles to use
Serif
Sans Serif

Requirements
Must have
• The Company logo and company colors.
Nice to have
• - Our tag line: "Revolutionizing IT Services" or "Revolutionizing the way IT services are delivered."
• - Also I really like the idea of nature and technology together blending which is sort of where my logo came from so integrating that somehow onto the business cards would be great.

```html
<!DOCTYPE html>
<html lang="en">
<head>
<meta charset="utf-8">
<title>Quillbrook Networks Ltd. – Business Card</title>
<link rel="stylesheet" href="https://fonts.googleapis.com/css2?family=Open+Sans:wght@400;600;700&display=swap">
<style>
  :root {
    --backdrop: #3c3c3d;
    --card-white: #ffffff;
    --panel-grey: #616264;
    --brand-blue: #1ba1dc;
    --text-light: #ffffff;
    --text-dark: #555658;
    --pattern-tint: #e6f4fb;
    --pattern-tint-soft: #f4fafd;
  }
  * { margin: 0; padding: 0; box-sizing: border-box; }
  html, body {
    width: 1105px;
    height: 1200px;
    overflow: hidden;
    background: var(--backdrop);
    font-family: "Open Sans", Arial, sans-serif;
  }
  .canvas { position: relative; width: 1105px; height: 1200px; }

  .card {
    position: absolute;
    left: 196px;
    width: 720px;
    height: 412px;
    background: var(--card-white);
    overflow: hidden;
  }
  .card--front { top: 146px; }
  .card--back { top: 602px; }

  .front-shape { position: absolute; inset: 0; }

  .contact {
    position: absolute;
    left: 37px;
    top: 0;
    color: var(--text-light);
  }
  .contact__name {
    position: absolute;
    top: 103px;
    font-size: 28px;
    font-weight: 600;
    white-space: nowrap;
  }
  .contact__address {
    position: absolute;
    top: 163px;
    font-size: 18.5px;
    line-height: 26px;
    font-weight: 400;
    white-space: nowrap;
  }
  .contact__list {
    position: absolute;
    top: 222px;
    list-style: none;
    font-size: 18.5px;
    line-height: 27.5px;
    white-space: nowrap;
  }
  .contact__item { display: flex; align-items: center; }
  .contact__icon { width: 16px; height: 16px; margin-right: 11px; flex: none; }

  .brand {
    position: absolute;
    left: 442px;
    top: 168px;
    display: flex;
    align-items: center;
    gap: 12px;
  }
  .brand__mark {
    width: 40px; height: 40px;
    border: 3px solid var(--brand-blue);
    border-radius: 50%;
    flex: none;
  }
  .brand__name {
    color: var(--brand-blue);
    font-size: 25px;
    line-height: 30px;
    font-weight: 600;
  }

  .back-pattern {
    position: absolute;
    inset: 0;
    background: linear-gradient(135deg, var(--pattern-tint-soft), var(--pattern-tint) 50%, var(--pattern-tint-soft));
  }
  .back-brand {
    position: absolute;
    left: 0; right: 0;
    top: 176px;
    text-align: center;
    color: var(--brand-blue);
    font-size: 30px;
    font-weight: 600;
  }
  .tagline {
    position: absolute;
    left: 0; right: 0;
    top: 323px;
    text-align: center;
    color: var(--text-dark);
    font-size: 19px;
    font-weight: 600;
  }
</style>
</head>
<body>
<main class="canvas">

  <section class="card card--front">
    <svg class="front-shape" width="720" height="412" viewBox="0 0 720 412">
      <polygon points="0,0 398,0 290,206 398,412 0,412" fill="var(--panel-grey)"/>
      <polyline points="415,0 306,206 420,412" fill="none" stroke="var(--brand-blue)" stroke-width="7"/>
    </svg>

    <div class="contact">
      <p class="contact__name">Daniel Hartley</p>
      <p class="contact__address">4821 Cedarview Road<br>Burnaby, BC V5G 2K9</p>
      <ul class="contact__list">
        <li class="contact__item">
          <svg class="contact__icon" viewBox="0 0 16 16"><path d="M3.5 1 L6 1.5 L6.8 5 L5 6.3 C5.9 8.3 7.7 10.1 9.7 11 L11 9.2 L14.5 10 L15 12.5 C15 14 13.8 15 12.4 15 C6.4 14.6 1.4 9.6 1 3.6 C1 2.2 2 1 3.5 1 Z" fill="var(--text-light)"/></svg>
          <span>604-555-0148</span>
        </li>
        <li class="contact__item">
          <svg class="contact__icon" viewBox="0 0 16 16"><rect x="1" y="3.5" width="14" height="9.5" fill="var(--text-light)"/><polyline points="1.5,4 8,9 14.5,4" fill="none" stroke="var(--panel-grey)" stroke-width="1.3"/></svg>
          <span>dhartley@quillbrook.me</span>
        </li>
        <li class="contact__item">
          <svg class="contact__icon" viewBox="0 0 16 16"><circle cx="8" cy="8" r="7" fill="var(--text-light)"/><path d="M4 5 C6 5 6 7 7.5 8 C6.5 10 5 10.5 5 13 M10 3 C9 4.5 10.5 6 12 6 C12.5 8 10.5 9 11 11" fill="none" stroke="var(--panel-grey)" stroke-width="1.4"/></svg>
          <span>www.quillbrook.me</span>
        </li>
      </ul>
    </div>

    <div class="brand">
      <span class="brand__mark"></span>
      <p class="brand__name">Quillbrook<br>Networks Ltd.</p>
    </div>
  </section>

  <section class="card card--back">
    <div class="back-pattern" role="img" aria-label="Faint light-blue repeating hexagon and cube pattern covering the card"></div>
    <p class="back-brand">Quillbrook Networks Ltd.</p>
    <p class="tagline">Revolutionizing IT Services</p>
  </section>

</main>
</body>
</html>
```